Broschüren-Design für Unternehmen, das die Begrünung von Bürogebäuden anbietet
Wir sind mit der Zusammenarbeit mit inkmolde äußerst zufrieden. Vielen Dank für das ganze Mitdenken und die wichtigen Rückfragen an uns (Format, Layout, Farben, Papierwahl)! :)
Zielgruppe
Unser Kerngeschäft besteht in der Begrünung von Bürogebäuden.
Das heißt, wir liefern und pflegen exotische und tropische immergrüne Planzen für zum Beispiel Eingangsbereiche, Atrien, sowie Einzel- und Großraumbüros.
Die Zielgruppe besteht fast ausschließlich aus gewerblichen Kunden.
Aufgabenstellung
Die Vorlage ist ein grober Entwurf und Vorschlag von uns. Es darf davon auch gerne abgewichen werden.
Die Broschüre soll uns als Unterstützung für Erstgespräche bei potentiellen Neukunden dienen und verbleibt beim Kunden. Sie soll unsere Firma, uns als Menschen und unsere Produkte und Dienstleistung kurz präsentieren und einen guten Eindruck hinterlassen.
Danach wünschen wir uns idealerweise eine Kontaktaufnahme durch den Kunden selbst.

```html
<!DOCTYPE html>
<html lang="de">
<head>
<meta charset="utf-8">
<title>Broschüre – Pflege &amp; Neubegrünung</title>
<link rel="stylesheet" href="https://fonts.googleapis.com/css2?family=Alegreya+Sans:ital,wght@0,400;0,500;0,700;1,800&display=swap">
<style>
  :root {
    --paper: #ffffff;
    --panel-grey: #f1f0ee;
    --ink: #1d1d1b;
    --mark-line: #ffffff;
    --caption-bg: rgba(255,255,255,0.92);
  }
  * { margin: 0; padding: 0; box-sizing: border-box; }
  html, body { width: 1200px; height: 400px; overflow: hidden; background: var(--paper); }
  body { font-family: "Alegreya Sans", sans-serif; color: var(--ink); }
  .spread { position: relative; width: 1200px; height: 400px; overflow: hidden; }
  .block { position: absolute; }
  .photo { position: absolute; }
  .photo--atrium-tree { left: 0; top: 0; width: 235px; height: 400px;
    background: linear-gradient(160deg, #e9ecd9 0%, #9fb27a 40%, #5d6e3d 75%, #7a5a44 100%); }
  .photo--tropical-bed { left: 592px; top: 0; width: 208px; height: 190px;
    background: linear-gradient(170deg, #d8dcd3 0%, #7c9a58 45%, #3e5a2c 100%); }
  .photo--palm { left: 235px; top: 190px; width: 165px; height: 210px;
    background: linear-gradient(180deg, #f4f3ef 0%, #6f8c73 45%, #3f5c48 75%, #d0623e 100%); }
  .photo--ficus-pot { left: 400px; top: 297px; width: 136px; height: 103px;
    background: linear-gradient(180deg, #d7dfe0 0%, #9bae8a 55%, #cf3c46 100%); }
  .photo--bonsai-pot { left: 650px; top: 297px; width: 150px; height: 103px;
    background: linear-gradient(180deg, #d6dedf 0%, #8fa571 55%, #cf3c46 100%); }
  .photo--moss-wall { left: 800px; top: 0; width: 400px; height: 400px;
    background: linear-gradient(100deg, #58643a 0%, #b9a784 30%, #6c7a3e 50%, #c5b48f 70%, #5b4a3a 100%); }

  .panel--care { left: 235px; top: 0; width: 165px; height: 190px; background: var(--paper); padding: 17px 17px 0 17px; }
  .panel--team { left: 400px; top: 0; width: 192px; height: 190px; background: var(--panel-grey); }
  .panel--new { left: 400px; top: 190px; width: 400px; height: 107px; background: var(--paper); padding: 19px 20px 0 19px; }
  .panel--info { left: 536px; top: 297px; width: 114px; height: 103px; background: var(--panel-grey); }

  .headline { font-weight: 800; font-style: italic; font-size: 18px; line-height: 22px; letter-spacing: -0.1px; }
  .body-text { font-size: 7.4px; line-height: 8.8px; text-align: justify; }
  .body-text p + p { margin-top: 8.8px; }
  .panel--care .body-text { margin-top: 24px; }

  .team-title { position: absolute; left: 54px; top: 23px; font-weight: 700; font-size: 8.4px; line-height: 9.4px; }
  .team-text { position: absolute; left: 21px; top: 61px; width: 144px; font-size: 6.6px; line-height: 7.8px; text-align: justify; }
  .team-text p + p { margin-top: 2px; }

  .mark { position: absolute; border: 1.5px solid var(--mark-line); border-radius: 50%; }
  .panel--team .mark { left: 14px; top: 15px; width: 32px; height: 32px; }
  .panel--info .mark { left: 27px; top: 12px; width: 60px; height: 60px; border-width: 3px; }

  .panel--new .body-text { margin-top: 17px; text-align: left; }
  .panel--new .body-text p + p { margin-top: 3px; }

  .info-label { position: absolute; left: 0; right: 0; top: 78px; text-align: center; font-weight: 500; font-size: 9px; }

  .caption { position: absolute; background: var(--caption-bg); font-size: 4.6px; line-height: 5.6px; display: flex; align-items: center; }
  .caption .mark { width: 26px; height: 26px; }
  .caption span { position: relative; }
  .caption--oldest { left: 0; top: 306px; width: 126px; height: 17px; padding-left: 44px; }
  .caption--oldest .mark { left: 12px; top: -4px; }
  .caption--tallest { left: 235px; top: 360px; width: 125px; height: 18px; padding-left: 46px; }
  .caption--tallest .mark { left: 12px; top: -6px; }
  .caption--tropical { left: 675px; top: 165px; width: 125px; height: 17px; padding-left: 45px; }
  .caption--tropical .mark { left: 5px; top: -7px; }
  .caption--moss { left: 1077px; top: 333px; width: 123px; height: 17px; padding-left: 45px; }
  .caption--moss .mark { left: 4px; top: -7px; }
</style>
</head>
<body>
<main class="spread">
  <div class="photo photo--atrium-tree" role="img" aria-label="Großer Zimmerbaum in einem Bürofoyer mit Pflanzbeet"></div>
  <div class="caption caption--oldest"><span class="mark"></span><span>Einer unserer ältesten:<br>Gepflanzt 1978, stolze 41 Jahre alt</span></div>

  <section class="block panel--care">
    <h2 class="headline">Pflege &amp; Wartung<br>Bestandspflanzen</h2>
    <div class="body-text">
      <p>Sie kommen morgens in die Firma, öffnen die Tür zum Büro, setzen sich, und haben bereits eine Grünpflanze vor sich?</p>
      <p>Hervorragend! Gießen, Düngen, Schneiden, Abstauben, Umtopfen: kurzum die Rundumversorgung Ihrer Pflanzen bieten wir Ihnen gerne für Ihren existierenden kleinen Urwald an.</p>
    </div>
  </section>

  <section class="block panel--team">
    <span class="mark"></span>
    <h3 class="team-title">Wir kümmern uns mit<br>unserem Team gerne um<br>Ihre bestehenden Pflanzen.</h3>
    <div class="team-text">
      <p>Unsere ältesten Schützlinge wurden in den 1970ern gepflanzt und erfreuen sich auch in ihrem bald 50. Lebensjahr bester Gesundheit.</p>
      <p>Unsere kleinsten Grünen sind kaum höher als ein Steckling, unsere Größten strecken sich in Eingangshallen bis 5 Meter in die Höhe.</p>
      <p>Manche unserer Kunden erfreuen sich in ihrer Hauptverwaltung an 2000 Pflanzen und das typische Startup ist stolz auf die ersten 5 grünen Mitbewohner.</p>
      <p>Wir sind spezialisiert auf die Innenraumbegrünung, die wir mögen, können und lieben.</p>
      <p>Vielleicht auch bald in Ihren Räumlichkeiten?</p>
    </div>
  </section>

  <div class="photo photo--tropical-bed" role="img" aria-label="Dichte tropische Bepflanzung mit Dracaena und Blattpflanzen"></div>
  <div class="caption caption--tropical"><span class="mark"></span><span>Infos zum Bild</span></div>

  <div class="photo photo--palm" role="img" aria-label="Fünf Meter hohe Zimmerpalme in einem Empfangsbereich mit roten Sesseln"></div>
  <div class="caption caption--tallest"><span class="mark"></span><span>Einer unserer größten: 5 Meter</span></div>

  <section class="block panel--new">
    <h2 class="headline">Neubegrünung &amp; Lieferung</h2>
    <div class="body-text">
      <p>Sie kommen morgens in die Firma, öffnen die Tür zum Büro, setzen sich, und starren erst einmal auf eine kahle Wand? Zeit, etwas Farbe in Ihr Büro zu bringen. Und am besten natürlich grün! Pflanzen im Büro lockern die Arbeitsatmosphäre auf und sorgen dafür, dass sich alle wohlfühlen.</p>
      <p>Wir kümmern uns um die Neubegrünung Ihrer Büroräumlichkeiten.</p>
    </div>
  </section>

  <div class="photo photo--ficus-pot" role="img" aria-label="Gummibaum in rotem Pflanzgefäß vor Glasfassade"></div>
  <section class="block panel--info">
    <span class="mark"></span>
    <p class="info-label">Informativer Text</p>
  </section>
  <div class="photo photo--bonsai-pot" role="img" aria-label="Kleiner Baum mit knorrigem Stamm in rotem Pflanzgefäß"></div>

  <div class="photo photo--moss-wall" role="img" aria-label="Café mit Mooswänden, Holztischen und Stühlen"></div>
  <div class="caption caption--moss"><span class="mark"></span><span>Infos zum Bild</span></div>
</main>
</body>
</html>
```